Packaging design for a reclosable bag for our product

We have a logo, and we need to put it on packaging for our product and while we want the look to be simple, we want it to follow good design principles and also contain spaces for other product descriptions.

There will be 5 sizes at launch so I'd like 5 variations, one for each size.

I've included a few mockups of the type of bag that I made but they are all just rough ideas that I had.

I want the brand to look scientific and methodical and even a bit quirky, as in "wow this is a serious product but also a bit unusual."

```html
<!DOCTYPE html>
<html lang="en">
<head>
<meta charset="utf-8">
<title>QV4 Bias Lighting Pouch</title>
<link href="https://fonts.googleapis.com/css2?family=Montserrat:wght@300;400;700&display=swap" rel="stylesheet">
<style>
  :root {
    --backdrop: #c9c9c9;
    --pouch: #f1f1f1;
    --pouch-edge: #e4e4e4;
    --seal-line: #d6d6d6;
    --ink: #0b0b0b;
    --paper: #ffffff;
  }
  * { margin: 0; padding: 0; box-sizing: border-box; }
  html, body {
    width: 1200px; height: 789px; overflow: hidden;
    background: var(--backdrop);
    font-family: "Montserrat", Arial, sans-serif;
  }
  .stage { position: relative; width: 1200px; height: 789px; }
  .pouch {
    position: absolute; left: 411px; top: 150px;
    width: 378px; height: 490px;
    background: var(--pouch);
    box-shadow: 0 6px 14px rgba(0,0,0,0.12);
  }
  .pouch-surface { position: absolute; inset: 0; width: 100%; height: 100%; }
  .seal-top {
    position: absolute; left: 0; right: 0; top: 0; height: 16px;
    border-bottom: 1px solid var(--seal-line);
    background: repeating-linear-gradient(to bottom, var(--pouch) 0 3px, var(--pouch-edge) 3px 4px);
  }
  .seal-side {
    position: absolute; top: 16px; bottom: 0; width: 14px;
    background: repeating-linear-gradient(to right, var(--pouch) 0 3px, var(--pouch-edge) 3px 4px);
  }
  .seal-side.left { left: 0; }
  .seal-side.right { right: 0; }
  .brand {
    position: absolute; left: 0; right: 0; top: 72px;
    display: flex; align-items: center; justify-content: center; gap: 14px;
  }
  .brand-dot { width: 26px; height: 26px; border-radius: 50%; background: var(--ink); }
  .brand-name {
    font-weight: 700; font-size: 62px; color: var(--ink); letter-spacing: -1px; line-height: 1;
  }
  .product-title {
    position: absolute; left: 0; right: 0; top: 228px;
    text-align: center; font-weight: 700; font-size: 35px; line-height: 1.12;
    color: var(--ink); letter-spacing: 0.5px;
  }
  .size-badge { position: absolute; left: 143px; top: 340px; width: 118px; height: 84px; }
  .spec {
    position: absolute; left: 0; right: 0; top: 438px;
    text-align: center; font-weight: 400; font-size: 8.5px; line-height: 1.35;
    color: var(--ink); letter-spacing: 0.3px;
  }
  .maker {
    position: absolute; left: 6px; bottom: 14px;
    display: flex; align-items: center; gap: 4px;
  }
  .maker-square { width: 30px; height: 30px; background: var(--ink); }
  .maker-name { font-weight: 400; font-size: 8px; color: var(--ink); }
</style>
</head>
<body>
<main class="stage">
  <section class="pouch" aria-label="QV4 bias lighting pouch, 5 metre">
    <svg class="pouch-surface" viewBox="0 0 378 490" role="img" aria-label="Faint overlapping scallop pattern printed across the pouch">
      <rect width="378" height="490" fill="#efefef"/>
    </svg>
    <div class="seal-top"></div>
    <div class="seal-side left"></div>
    <div class="seal-side right"></div>

    <div class="brand">
      <span class="brand-dot"></span>
      <span class="brand-name">QV4</span>
    </div>

    <h1 class="product-title">BIAS<br>LIGHTING</h1>

    <svg class="size-badge" viewBox="0 0 118 84" aria-label="5m">
      <path d="M10 52 C2 30 22 4 58 3 C96 2 118 18 115 38 C112 62 84 82 52 82 C28 82 15 70 10 52 Z" fill="var(--ink)"/>
      <text x="56" y="55" text-anchor="middle" fill="var(--paper)" font-family="Montserrat, Arial, sans-serif" font-weight="300" font-size="31">5m</text>
    </svg>

    <p class="spec">6500K WHITE BIAS LIGHTING<br>SIMULATED D95 CRI 90+</p>

    <div class="maker">
      <span class="maker-square"></span>
      <span class="maker-name">Orrin</span>
    </div>
  </section>
</main>
</body>
</html>
```